Web site for radio show

I've got a radio show starting on OrbitalWave and need a web site for it. I am familiar with WordPress, so I'd like to get a design for a WordPress-based web site for the show.

I'm also posting a logo project to be done at the same time.

The best radio show web site I've seen is the Cosmic Tuesday site (www.cosmictuesday-example.com). That's a good model but I don't want to start with that much complexity and content. The initial site that I'd like you to design would have the following parts:
- Upcoming shows
- Past shows (including links to authors, their web sites, and their books)
- Twitter feed
- Blog
- About
- ...and anything else you think would be necessary

For colors, I'd like it to be consistent with my personal web site: www.kellaway-ventures-example.com

Target Market(s)

The target market for this show is mid- to upper-level managers

Industry/Entity Type

Radio

Requirements
Must have
• The project has to proceed in (at least) two stages: a first rough layout, and a second finished design. Whether you want a third stage in between with look and feel options is up to you.

```html
<!DOCTYPE html>
<html lang="en">
<head>
<meta charset="utf-8">
<title>Kellaway Show</title>
<link href="https://fonts.googleapis.com/css2?family=Open+Sans:wght@400;600;700&family=Arimo:wght@400;700&display=swap" rel="stylesheet">
<style>
:root{
  --red:#d0202e;
  --ink:#333;
  --grey-band:#e6e6e6;
  --panel:#e9e9e9;
  --line:#cfcfcf;
  --footer:#8a8a8a;
  --black:#000;
  --white:#fff;
  --link:#1a8fd0;
}
*{box-sizing:border-box;margin:0;padding:0}
html,body{width:1066px;height:1200px;overflow:hidden;background:var(--white);font-family:"Open Sans",sans-serif;color:var(--ink)}
.page{position:relative;width:1066px;height:1200px}
.abs{position:absolute}

/* header */
.brand{left:154px;top:20px;width:130px;color:var(--red);font-weight:700;font-size:20px;line-height:21px;letter-spacing:.5px}
.search{left:550px;top:10px;width:196px;height:22px;background:#eee;border:1px solid #ddd;font-family:Arimo,sans-serif;font-style:italic;font-size:10px;color:#666;padding:4px 7px}
.search svg{position:absolute;right:6px;top:3px}
.social-top{left:764px;top:12px;display:flex;gap:5px}
.social-top span{width:20px;height:20px;border-radius:50%;background:#222;display:block}
.nav{left:548px;top:50px;display:flex;gap:22px;font-size:14px;color:#333;letter-spacing:.2px}

/* hero */
.hero{left:0;top:87px;width:1066px;height:387px;background:var(--black)}
.hero-photo{left:0;top:0;width:648px;height:387px;background:radial-gradient(ellipse at 50% 45%,#c9ccd4 0%,#6e7486 35%,#262a36 65%,#000 90%)}
.hero-title{left:698px;top:165px;color:var(--white);font-size:29px;line-height:31px;letter-spacing:1px}
.dots{left:778px;top:363px;display:flex;gap:13px}
.dots i{width:17px;height:4px;background:var(--white);display:block}
.dots i.on{background:var(--red)}

/* section heads */
.sec-head{height:39px;background:var(--panel);border-top:4px solid var(--red);font-size:17px;padding:10px 9px 0;color:#222}
.about{left:153px;top:501px;width:255px}
.about-photo{margin-top:3px;height:100px;background:linear-gradient(100deg,#777 0%,#aaa 35%,#6b4a3a 65%,#3a1d1a 100%)}
.about p{margin-top:11px;font-size:9px;line-height:14px;text-align:justify;color:#444}
.btn-red{display:block;margin:6px 0 0 auto;width:90px;height:21px;background:var(--red);color:var(--white);font-size:11px;font-weight:600;text-align:center;line-height:21px;border-radius:2px}

.upcoming{left:421px;top:501px;width:493px}
.arrows{position:absolute;right:4px;top:5px;display:flex;gap:2px}
.arrows span{width:28px;height:28px;background:#000;display:flex;align-items:center;justify-content:center}
.shows{left:421px;top:542px;width:493px;display:grid;grid-template-columns:240px 240px;gap:5px 13px}
.show{height:89px;background:linear-gradient(#fff,#dcdcdc);border:1px solid #ccc;position:relative}
.show .thumb{position:absolute;left:12px;top:9px;width:93px;height:70px}
.show .date{position:absolute;left:117px;top:11px;color:var(--red);font-size:12px}
.show .txt{position:absolute;left:117px;top:28px;font-size:11px;line-height:14px;color:#444}
.btn-dark{position:absolute;left:117px;top:62px;width:61px;height:14px;background:#3a3a3a;color:var(--white);font-size:7.5px;text-align:center;line-height:14px;border-radius:1px;font-weight:600}

/* grey band */
.band{left:0;top:728px;width:1066px;height:213px;background:var(--grey-band)}
.mini-head{font-size:13px;font-weight:600;color:#222}
.mini-arrows{position:absolute;display:flex;gap:1px}
.mini-arrows span{width:13px;height:12px;border:1px solid #555;background:#f4f4f4}
.blog-card{left:152px;width:425px;height:70px;background:var(--white);border:1px solid #ccc}
.blog-card .thumb{position:absolute;left:3px;top:3px;width:79px;height:62px}
.blog-card h3{position:absolute;left:92px;top:4px;font-family:Arimo,sans-serif;font-weight:400;font-size:11px;color:var(--red)}
.blog-card p{position:absolute;left:92px;top:18px;width:326px;font-family:Arimo,sans-serif;font-size:9px;line-height:12px;color:#555}
.share{position:absolute;top:46px;display:flex;gap:3px;font-family:Arimo,sans-serif;font-size:8px}
.share b{border:1px solid #ccc;background:#f6f6f6;padding:1px 5px;font-weight:700;color:#333}
.share em{font-style:normal;border:1px solid #ccc;padding:1px 3px;color:#555}
.past-card{top:768px;width:158px;height:153px;background:var(--white);border:1px solid #ccc;text-align:center}
.past-card h4{font-weight:400;font-size:11px;margin-top:6px;color:#333}
.past-card .thumb{width:126px;height:69px;margin:5px auto 0}
.past-card .auth{font-size:11px;margin-top:3px}
.past-card .url{font-size:7.5px;color:var(--red);margin-top:3px}
.past-card svg{margin-top:5px}

/* tweets */
.tw-title{left:314px;top:948px;font-size:13px;font-weight:600;color:#222}
.follow{left:728px;top:951px;font-family:Arimo,sans-serif;font-size:9px;color:var(--link)}
.tw-icon{width:34px;height:34px;border-radius:6px;background:#2ba3e6}
.tweet{left:379px;width:384px;height:37px;border:1px solid #ccc;font-family:Arimo,sans-serif;font-size:9px;line-height:12px;color:#444;padding:5px 10px}
.tweet i{color:var(--red)}
.tweet b{font-weight:400;color:#111}

/* footer */
.footer{left:0;top:1086px;width:1066px;height:114px;background:var(--footer)}
.foot-links{left:322px;top:12px;display:flex;gap:19px;font-size:13px;color:var(--white)}
.partner{left:154px;top:48px;color:#1f2f6b;font-weight:700;font-size:20px}
.copy{left:435px;top:58px;font-family:Arimo,sans-serif;font-size:10px;color:var(--white)}
.foot-social{left:733px;top:46px;display:flex;gap:7px}
.foot-social span{width:31px;height:31px;border-radius:50%;border:2px solid #bbb;display:block}
</style>
</head>
<body>
<div class="page">

  <header>
    <div class="abs brand">KELLAWAY SHOW</div>
    <div class="abs search">search
      <svg width="14" height="14" viewBox="0 0 14 14"><circle cx="5.5" cy="5.5" r="4.2" fill="none" stroke="#555" stroke-width="1.6"/><line x1="8.6" y1="8.6" x2="13" y2="13" stroke="#555" stroke-width="1.8"/></svg>
    </div>
    <div class="abs social-top" aria-label="Social links"><span></span><span></span><span></span><span></span><span></span><span></span></div>
    <nav class="abs nav"><span>LISTEN WATCH</span><span>READ</span><span>EDUCATE</span><span>DONATE ABOUT</span></nav>
  </header>

  <section class="abs hero">
    <div class="abs hero-photo" role="img" aria-label="Close-up of a chrome studio microphone with headphones"></div>
    <div class="abs hero-title">KELLAWAY<br>SHOW</div>
    <div class="abs dots"><i class="on"></i><i></i><i></i><i></i></div>
  </section>

  <section class="abs about">
    <div class="sec-head">ABOUT US</div>
    <div class="about-photo" role="img" aria-label="Presenter at a radio studio mixing desk"></div>
    <p>Daniel Kellaway is a Professor of Practice at the Halden School where he teaches Innovation and Product Development in Halden's undergraduate, MBA, and</p>
    <span class="btn-red">READ MORE</span>
  </section>

  <section class="abs upcoming">
    <div class="sec-head">UPCOMING SHOWS</div>
    <div class="arrows">
      <span><svg width="12" height="18"><polyline points="10,1 2,9 10,17" fill="none" stroke="#fff" stroke-width="1.6"/></svg></span>
      <span><svg width="12" height="18"><polyline points="2,1 10,9 2,17" fill="none" stroke="#fff" stroke-width="1.6"/></svg></span>
    </div>
  </section>
  <div class="abs shows">
    <article class="show"><div class="thumb" role="img" aria-label="Guest speaking into a studio microphone" style="background:linear-gradient(135deg,#9bb3c9,#4a6a8c)"></div><div class="date">Feb.25, 2014</div><div class="txt">Praesent vestibulum<br>aenean nonummy</div><span class="btn-dark">READ MORE</span></article>
    <article class="show"><div class="thumb" role="img" aria-label="Studio microphone on a blue background" style="background:linear-gradient(90deg,#222,#8aa4c0)"></div><div class="date">Feb.15, 2014</div><div class="txt">Praesent vestibulum<br>aenean nonummy</div><span class="btn-dark">READ MORE</span></article>
    <article class="show"><div class="thumb" role="img" aria-label="Host in headphones reading a script" style="background:linear-gradient(135deg,#555,#222)"></div><div class="date">Feb.12, 2014</div><div class="txt">Praesent vestibulum<br>aenean nonummy</div><span class="btn-dark">READ MORE</span></article>
    <article class="show"><div class="thumb" role="img" aria-label="Presenter in a broadcast studio" style="background:linear-gradient(135deg,#2a3a5a,#b89a7a)"></div><div class="date">Feb.19, 2014</div><div class="txt">Praesent vestibulum<br>aenean nonummy</div><span class="btn-dark">READ MORE</span></article>
  </div>

  <div class="abs band"></div>
  <div class="abs mini-head" style="left:152px;top:747px">BLOG</div>
  <div class="mini-arrows" style="left:549px;top:748px"><span></span><span></span></div>
  <article class="abs blog-card" style="top:768px">
    <div class="thumb" role="img" aria-label="Business people in an office" style="background:linear-gradient(135deg,#c9d3de,#5a6878)"></div>
    <h3>The Angriest BRIKO Minifigs</h3>
    <p>BRIKO friends is the latest attempt by BRIKO to attract young girls to the brand. Commerce Weekly covered the launch extensively and well in a cover story</p>
    <div class="share" style="left:98px"><b>+1</b><em>0</em></div>
    <div class="share" style="left:172px"><b>Post</b><em>0</em></div>
    <div class="share" style="left:258px"><b>Share</b></div>
  </article>
  <article class="abs blog-card" style="top:850px">
    <div class="thumb" role="img" aria-label="Man presenting at a whiteboard" style="background:linear-gradient(135deg,#d8dde2,#7a8088)"></div>
    <h3>The Angriest BRIKO Minifigs</h3>
    <p>BRIKO friends is the latest attempt by BRIKO to attract young girls to the brand. Commerce Weekly covered the launch extensively and well in a cover story</p>
    <div class="share" style="left:98px"><b>+1</b><em>0</em></div>
    <div class="share" style="left:172px"><b>Post</b><em>0</em></div>
    <div class="share" style="left:258px"><b>Share</b></div>
  </article>

  <div class="abs mini-head" style="left:589px;top:748px">PAST SHOWS</div>
  <div class="mini-arrows" style="left:883px;top:749px"><span></span><span></span></div>
  <article class="abs past-card" style="left:587px">
    <h4>PRAESENT VESTIBULUM</h4>
    <div class="thumb" role="img" aria-label="Author portrait in monochrome" style="background:linear-gradient(135deg,#111,#777)"></div>
    <div class="auth">AUTHORS</div>
    <div class="url">www.kellaway-ventures-example.com</div>
    <svg width="16" height="16" viewBox="0 0 16 16"><rect x="1" y="1" width="11" height="13" fill="#666"/><path d="M10 8v5M7.5 11l2.5 2.5 2.5-2.5" stroke="#333" stroke-width="1.6" fill="none"/></svg>
  </article>
  <article class="abs past-card" style="left:745px;width:167px">
    <h4>PRAESENT VESTIBULUM</h4>
    <div class="thumb" role="img" aria-label="Author portrait with headphones" style="background:linear-gradient(135deg,#1b2a4a,#8fa6c4)"></div>
    <div class="auth">AUTHORS</div>
    <div class="url">www.kellaway-ventures-example.com</div>
    <svg width="16" height="16" viewBox="0 0 16 16"><rect x="1" y="1" width="11" height="13" fill="#666"/><path d="M10 8v5M7.5 11l2.5 2.5 2.5-2.5" stroke="#333" stroke-width="1.6" fill="none"/></svg>
  </article>

  <div class="abs tw-title">Latest Tweets</div>
  <div class="abs follow">+ Follow</div>
  <div class="abs tw-icon" style="left:314px;top:977px"></div>
  <div class="abs tweet" style="top:975px"><i>@Nimbus is Local!</i> Mes cuml dia. Sted in lacus utertoenim asci aliiqt sit amet. a. Sted in lacus utertoenim Mes cuml dia. Sted in lacus utertoenim asci aliiqt sit amet. <b>21/03/214</b></div>
  <div class="abs tw-icon" style="left:316px;top:1025px"></div>
  <div class="abs tweet" style="top:1023px;left:380px"><i>@Nimbus is Local!</i> Mes cuml dia. Sted in lacus utertoenim asci aliiqt sit amet. a. Sted in lacus utertoenim Mes cuml dia. Sted in lacus utertoenim asci aliiqt sit amet. <b>21/03/214</b></div>

  <footer class="abs footer">
    <nav class="abs foot-links"><span>Contact</span><span>Supporters</span><span>Newsletter</span><span>Policies</span><span>Available from TuneStore</span></nav>
    <div class="abs partner">OrbitalWave</div>
    <div class="abs copy">© 2014 Kellaway Show All Rights Reserved</div>
    <div class="abs foot-social" aria-label="Social links">
      <span style="background:#2aa6d8"></span><span style="background:#3b5a99"></span><span style="background:#666"></span><span style="background:#d8578b"></span><span style="background:#f4f4f4"></span>
    </div>
  </footer>

</div>
</body>
</html>
```